Business Card Design for The Lending Nest Inc.

We need a business card design for our mortgage company: "The Lending Nest Inc."

Need to have Social Media Account on there as a possibility

```html
<!DOCTYPE html>
<html lang="en">
<head>
<meta charset="utf-8">
<title>The Lending Nest Inc. – Business Card</title>
<link rel="stylesheet" href="https://fonts.googleapis.com/css2?family=Lato:wght@300;400;700&family=Montserrat:wght@400;500&display=swap">
<style>
  :root {
    --page: #ffffff;
    --card-dark: #1b1b1c;
    --brand-blue: #1a5aa6;
    --deep-blue: #2c3f6b;
    --slate-blue: #3d4f70;
    --social-blue: #2f63ad;
    --icon-blue: #3f82d0;
    --light-text: #dcdcdc;
  }
  * { margin: 0; padding: 0; box-sizing: border-box; }
  html, body {
    width: 1200px; height: 1200px; overflow: hidden;
    background: var(--page);
  }
  .canvas { position: relative; width: 1200px; height: 1200px; }
  .card {
    position: absolute; left: 234px; width: 732px; height: 429px;
    background: var(--card-dark); overflow: hidden;
  }
  .card--front { top: 97px; }
  .card--back { top: 628px; }
  .card svg.shape { position: absolute; inset: 0; width: 100%; height: 100%; }
  .brand-mark {
    position: absolute; border-radius: 50%;
    border: 6px solid var(--brand-blue);
  }
  .brand-name {
    position: absolute; white-space: nowrap;
    font-family: "Lato", sans-serif; font-weight: 700;
    color: var(--brand-blue); line-height: 1;
  }
  .tagline {
    position: absolute; left: 322px; top: 112px;
    font-family: "Montserrat", sans-serif; font-weight: 500;
    font-size: 31px; letter-spacing: 2px; color: var(--deep-blue);
    white-space: nowrap;
  }
  .social-list { position: absolute; left: 33px; top: 153px; list-style: none; }
  .social-item { display: flex; align-items: center; height: 38px; margin-bottom: 18px; }
  .social-dot { width: 38px; height: 38px; border-radius: 50%; background: var(--icon-blue); flex: none; }
  .social-label {
    margin-left: 16px;
    font-family: "Montserrat", sans-serif; font-size: 20px; letter-spacing: 1.5px;
    color: var(--social-blue); white-space: nowrap;
  }
  .company-title {
    position: absolute; left: 233px; top: 30px;
    font-family: "Lato", sans-serif; font-weight: 400; font-size: 50px;
    color: var(--light-text); white-space: nowrap;
  }
  .contact { position: absolute; font-family: "Lato", sans-serif; font-weight: 300;
    font-size: 27px; color: var(--light-text); white-space: nowrap; line-height: 1; }
</style>
</head>
<body>
<main class="canvas">

  <section class="card card--front" aria-label="Business card front">
    <svg class="shape" viewBox="0 0 732 429" aria-hidden="true">
      <defs>
        <linearGradient id="frontWave" x1="0" y1="0" x2="0" y2="1">
          <stop offset="0" stop-color="#1a5aa6"/>
          <stop offset="1" stop-color="#3d4f70"/>
        </linearGradient>
      </defs>
      <path d="M0,355 C250,345 450,322 600,304 C670,296 705,292 732,295 L732,429 L0,429 Z" fill="url(#frontWave)"/>
    </svg>
    <div class="brand-mark" style="left:102px; top:12px; width:112px; height:112px;"></div>
    <div class="brand-name" style="left:232px; top:50px; font-size:38px;">The Lending Nest Inc.</div>
    <div class="tagline">Lending Nest Inc</div>
    <ul class="social-list">
      <li class="social-item"><span class="social-dot"></span><span class="social-label">YOUR SOCIAL FEED</span></li>
      <li class="social-item"><span class="social-dot"></span><span class="social-label" style="margin-left:25px">YOUR SOCIAL PAGE</span></li>
      <li class="social-item"><span class="social-dot"></span></li>
    </ul>
  </section>

  <section class="card card--back" aria-label="Business card back">
    <svg class="shape" viewBox="0 0 732 429" aria-hidden="true">
      <defs>
        <linearGradient id="backPanel" x1="0" y1="0" x2="1" y2="0">
          <stop offset="0" stop-color="#3d4f70"/>
          <stop offset="1" stop-color="#1e5aa0"/>
        </linearGradient>
      </defs>
      <path d="M0,0 L183,0 C162,60 142,125 146,200 C150,280 166,360 157,429 L0,429 Z" fill="url(#backPanel)"/>
    </svg>
    <div class="company-title">Lending Nest Inc</div>
    <div class="brand-mark" style="left:186px; top:91px; width:100px; height:100px;"></div>
    <div class="brand-name" style="left:300px; top:123px; font-size:33px;">The Lending Nest Inc.</div>
    <div class="contact" style="left:186px; top:220px;">4415-208-937 or 6230-517-804</div>
    <div class="contact" style="left:200px; top:262px;">Larkfield Road , Maren 3408</div>
    <div class="contact" style="left:213px; top:309px;">alex.reyes@lendingnest.com</div>
    <div class="contact" style="left:225px; top:350px;">www.lendingnest.com</div>
  </section>

</main>
</body>
</html>
```